Young, dynamic furniture company needs a new business card design

We require a new business card design for our modern furniture company which supplies furniture and appliances to the property and development market.
Oakridge Interiors has become one of the leading furniture & appliance suppliers to the property market withing London. With over 10 years experience, we have increased our business to supply not only private landlords and managing agents, but also property developers, housing associations and local councils.
We offer not only a complete range of furniture which includes beds, wardrobes, dining sets and sofas, but also a high quality, full delivery and assembly service to help you with all our furnishing needs.

Target Market(s)

Private landlords, estate agents, letting agents, property management companies

Industry/Entity Type

Business

Contact Information for Business Card

Name,
Title,
Address,
Mobile,
Telephone,
Fax, Website, email address

Font styles to use
Sans Serif

Colors
3176b5
0555a3
85abd2
cfdeed

Requirements
Must have
• All the above information for each of our staff, along with our logo

```html
<!DOCTYPE html>
<html lang="en">
<head>
<meta charset="utf-8">
<title>Oakridge Interiors – Business Card</title>
<link href="https://fonts.googleapis.com/css2?family=Open+Sans:wght@300;400;600;700&display=swap" rel="stylesheet">
<style>
  :root {
    --page-bg: #e9ecf0;
    --card-white: #ffffff;
    --card-white-shade: #eceef1;
    --ink: #3a3d42;
    --navy: #1d3f8f;
    --brand-blue: #3176b5;
    --deep-blue: #0555a3;
    --soft-blue: #85abd2;
    --pale-blue: #cfdeed;
    --back-dark: #1a3f86;
    --back-light: #2b5cab;
  }
  * { box-sizing: border-box; margin: 0; padding: 0; }
  html, body { width: 1200px; height: 780px; overflow: hidden; }
  body {
    background: var(--page-bg);
    font-family: "Open Sans", Arial, sans-serif;
    display: flex;
    align-items: center;
    justify-content: center;
    gap: 50px;
  }
  .card {
    width: 525px;
    height: 300px;
    border-radius: 16px;
    position: relative;
    overflow: hidden;
    box-shadow: 0 10px 28px rgba(20, 30, 50, 0.18);
  }

  /* Front */
  .card-front {
    background: linear-gradient(160deg, var(--card-white) 45%, var(--card-white-shade) 100%);
    color: var(--ink);
  }
  .brand {
    position: absolute;
    top: 34px;
    right: 36px;
    text-align: right;
  }
  .brand-mark {
    display: inline-block;
    width: 46px;
    height: 46px;
    background: var(--brand-blue);
    margin-bottom: 10px;
  }
  .brand-name {
    font-size: 17px;
    font-weight: 400;
    letter-spacing: 0.02em;
    text-transform: uppercase;
    color: var(--ink);
    line-height: 1.1;
  }
  .brand-tagline {
    font-size: 7.5px;
    letter-spacing: 0.08em;
    text-transform: uppercase;
    color: var(--ink);
    margin-top: 3px;
  }
  .person {
    position: absolute;
    left: 34px;
    bottom: 30px;
  }
  .person-name {
    font-size: 19px;
    font-weight: 700;
    text-transform: uppercase;
    color: var(--navy);
    letter-spacing: 0.01em;
  }
  .person-name .surname { color: var(--brand-blue); }
  .person-title {
    font-size: 12.5px;
    color: var(--ink);
    margin-bottom: 14px;
  }
  .contact-line {
    font-size: 12px;
    line-height: 1.65;
    color: var(--ink);
  }
  .contact-line .label { color: var(--deep-blue); font-weight: 600; }
  .contact-line .sep { color: var(--deep-blue); padding: 0 4px; }
  .contact-line .site-accent { color: var(--deep-blue); font-weight: 600; }
  .address { margin-top: 10px; }

  /* Back */
  .card-back {
    background: linear-gradient(135deg, var(--back-dark) 0%, var(--back-light) 55%, var(--back-dark) 100%);
    color: #ffffff;
    display: flex;
    flex-direction: column;
    justify-content: center;
    padding-left: 46px;
  }
  .back-name {
    font-size: 38px;
    font-weight: 400;
    text-transform: uppercase;
    letter-spacing: 0.01em;
    line-height: 1.05;
  }
  .back-tagline {
    font-size: 17px;
    font-weight: 300;
    text-transform: uppercase;
    letter-spacing: 0.02em;
    margin-top: 6px;
    color: #eef3fa;
  }
</style>
</head>
<body>

  <section class="card card-front" aria-label="Business card front">
    <div class="brand">
      <span class="brand-mark" aria-hidden="true"></span>
      <div class="brand-name">Oakridge Interiors</div>
      <div class="brand-tagline">Trade Furniture Solutions</div>
    </div>

    <div class="person">
      <div class="person-name">Marcus <span class="surname">Hallam</span></div>
      <div class="person-title">Managing Director</div>
      <p class="contact-line">
        <span class="label">T:</span> 020 7946 0321<span class="sep">|</span><span class="label">F:</span> 020 7946 0322<span class="sep">|</span><span class="label">M:</span> 07700 90 04 18
      </p>
      <p class="contact-line">
        <span class="label">E:</span> marcus@oakridge.co.uk<span class="sep">|</span>www.<span class="site-accent">oakridge</span>.co.uk
      </p>
      <p class="contact-line address">Trade Showroom &amp; Office<br>27B Fernhill Trade Park Eastbrook London, E9 4QT</p>
    </div>
  </section>

  <section class="card card-back" aria-label="Business card back">
    <div class="back-name">Oakridge Interiors</div>
    <div class="back-tagline">Trade Furniture Solutions</div>
  </section>

</body>
</html>
```